Pemberlux: Smart Quotes for Wine Lovers

Hello. I am completing book of quotes for wine lovers. Need the text formatted so that it is easy to read and aesthetically pleasing...modern, clean, smart. Number the pages. The cover is complete. Book is small square. 7.5 by 7.5 inches. If you want to show me first few pages that would be awesome. Thank you!
Updates

I edited the quotes so if you downloaded first ones, please grab these ones instead, thank you! 

Target Market(s)

wine lovers. Urban. Modern.

Industry/Entity Type

Quotes

Requirements
Should not have
• No color. black and white only.

```html
<!DOCTYPE html>
<html lang="en">
<head>
<meta charset="utf-8">
<title>Pemberlux: Smart Quotes for Wine Lovers</title>
<link rel="stylesheet" href="https://fonts.googleapis.com/css2?family=Overlock:ital,wght@1,700&family=Mulish:wght@400;700&display=swap">
<style>
  :root {
    --backdrop: #e4e4e4;
    --paper: #ffffff;
    --ink: #111111;
    --gutter: #555555;
    --mark-light: #ececec;
    --mark-dark: #b0b0b0;
  }
  * { box-sizing: border-box; margin: 0; padding: 0; }
  html, body {
    width: 1200px;
    height: 900px;
    overflow: hidden;
    background: var(--backdrop);
  }
  .spread {
    position: absolute;
    left: 60px;
    top: 187px;
    width: 1064px;
    height: 529px;
    display: flex;
    background: var(--paper);
    border: 1px solid var(--ink);
  }
  .page {
    position: relative;
    width: 532px;
    height: 100%;
    color: var(--ink);
  }
  .page + .page { border-left: 1px solid var(--gutter); }
  .page-mark {
    position: absolute;
    left: 244px;
    top: 27px;
    width: 44px;
    height: 82px;
    background: linear-gradient(to bottom, var(--mark-light), var(--mark-dark));
  }
  .page-number {
    position: absolute;
    left: 0;
    right: 0;
    top: 34px;
    text-align: center;
    font-family: "Mulish", sans-serif;
    font-weight: 700;
    font-size: 11px;
    line-height: 14px;
  }
  .quote {
    position: absolute;
    left: 0;
    right: 0;
    top: 147px;
    text-align: center;
    font-family: "Overlock", sans-serif;
    font-style: italic;
    font-weight: 700;
    font-size: 27px;
    line-height: 33px;
    font-variant-ligatures: none;
  }
  .bio {
    position: absolute;
    left: 30px;
    right: 30px;
    text-align: center;
    font-family: "Mulish", sans-serif;
    font-size: 12.5px;
    line-height: 18px;
  }
  .bio-name { font-weight: 700; }
  .page--left .bio { top: 410px; }
  .page--right .bio { top: 427px; }
</style>
</head>
<body>
  <main class="spread">
    <section class="page page--left">
      <div class="page-mark" role="img" aria-label="Wine glass page ornament"></div>
      <p class="page-number" style="left:244px;width:44px;right:auto;top:61px">-1-</p>
      <p class="quote">The discovery of a good wine is<br>increasingly better for mankind<br>than the discovery of a new star.<br>~ Matteo Orsaldi</p>
      <p class="bio"><span class="bio-name">Matteo di Giacomo Orsaldi</span> (1611 –1679)<br>Tuscan Baroque Painter, Vintner, Poet, Lutenist, Botanist,<br>Astronomer, Surveyor, Teacher, Collector, Traveller,<br>Letter Writer and Occasional Cook.</p>
    </section>
    <section class="page page--right">
      <div class="page-mark" role="img" aria-label="Wine glass page ornament"></div>
      <p class="page-number" style="left:244px;width:44px;right:auto;top:61px">-2-</p>
      <p class="quote">Be careful to trust a person who<br>does not like wine.<br>~ Henrik Bausch</p>
      <p class="bio"><span class="bio-name">Henrik Tobias Bausch (1874 –1931)</span><br>Danish Essayist, Gardener, Translator, Teacher, Lecturer,<br>and Occasional Playwright.</p>
    </section>
  </main>
</body>
</html>
```